Quran Jar

So I need help designing bespoke jars which will contain religious quotes.

So there will be three jars in total sold either individually or in two or as a three.

Each Jar will have different contents and preferably a different colour scheme.

I want the packaging to be customised with my branding and logo and to make the product stand out I am thinking of packing it further in a cotton bag with my branding.

```html
<!DOCTYPE html>
<html lang="en">
<head>
<meta charset="utf-8">
<title>Quran Jar – Label</title>
<link rel="stylesheet" href="https://fonts.googleapis.com/css2?family=Arimo:wght@400;700&family=Montserrat:wght@500&family=Cairo:wght@700&display=swap">
<style>
  :root{
    --green:#053d22;
    --green-text:#0a5a2a;
    --gold:#e6c977;
    --gold-light:#f6e38e;
    --gold-dark:#d4b466;
    --ink:#231f20;
    --white:#ffffff;
    --frame:#d9d9d9;
    --happy:#9bcb3c;
    --sad:#2e3192;
    --angry:#ed1c24;
    --anxious:#f7891e;
    --lonely:#93278f;
    --thankful:#00a0e3;
    --book:#b8a47c;
    --book-dark:#8e7b55;
  }
  html,body{margin:0;padding:0;overflow:hidden;background:var(--white);}
  .label{position:relative;width:1200px;height:1068px;background:var(--white);
    box-sizing:border-box;border:1px solid var(--frame);overflow:hidden;font-family:"Arimo",Arial,sans-serif;color:var(--ink);}
  .header{position:absolute;left:4px;top:4px;width:1192px;height:440px;background:var(--green);}
  .ornament{position:absolute;top:40px;width:230px;height:240px;opacity:.35;
    background:radial-gradient(circle at 30% 30%,var(--gold) 0,transparent 70%);}
  .ornament--left{left:40px;}
  .ornament--right{right:40px;transform:scaleX(-1);}
  .brand-mark{position:absolute;left:50%;top:50px;width:110px;height:110px;margin-left:-55px;border-radius:50%;background:var(--gold-light);}
  .brand-name{position:absolute;left:0;right:0;top:206px;text-align:center;font-family:"Montserrat",sans-serif;font-weight:500;font-size:54px;color:var(--gold);line-height:1;}
  .brand-tagline{position:absolute;left:0;right:0;top:274px;text-align:center;font-family:"Montserrat",sans-serif;font-weight:500;font-size:12px;letter-spacing:6px;color:var(--gold);}
  .product-title{position:absolute;left:0;right:0;top:296px;margin:0;text-align:center;font-weight:700;font-size:134px;line-height:1;letter-spacing:2px;
    background:linear-gradient(90deg,var(--gold-dark),var(--gold-light) 50%,var(--gold-dark));-webkit-background-clip:text;background-clip:text;color:transparent;}
  .subtitle{position:absolute;left:0;right:0;top:452px;margin:0;text-align:center;font-size:33px;letter-spacing:8px;line-height:1;}
  .headline{position:absolute;left:0;right:0;top:490px;margin:0;text-align:center;font-weight:700;font-size:80px;line-height:1;color:var(--green-text);}

  .emotion{position:absolute;height:50px;display:flex;align-items:center;}
  .emotion--left{left:0;}
  .emotion--right{left:600px;}
  .emotion .ar{font-family:"Cairo",sans-serif;font-weight:700;font-size:46px;direction:rtl;text-align:right;line-height:1;}
  .emotion--left .ar{width:208px;}
  .emotion--right .ar{width:200px;}
  .emotion .star{width:44px;height:44px;flex:none;}
  .emotion--left .star{margin:0 17px 0 29px;}
  .emotion--right .star{margin:0 15px 0 20px;}
  .emotion .en{font-size:45px;line-height:1;white-space:nowrap;}

  .book{position:absolute;left:462px;top:598px;width:186px;height:200px;border-radius:24px;
    background:linear-gradient(135deg,var(--book),var(--book-dark));}

  .banner{position:absolute;left:66px;top:833px;width:1070px;height:81px;
    background:linear-gradient(90deg,var(--gold-dark),var(--gold-light) 50%,var(--gold-dark));
    clip-path:polygon(2% 0,98% 0,100% 50%,98% 100%,2% 100%,0 50%);
    display:flex;align-items:center;justify-content:center;font-weight:700;font-size:47px;color:var(--ink);}
  .quote{position:absolute;left:0;right:0;top:932px;margin:0;text-align:center;font-size:25px;line-height:31px;}
</style>
</head>
<body>
<div class="label">
  <header class="header">
    <div class="ornament ornament--left" role="img" aria-label="Gold filigree corner ornament"></div>
    <div class="ornament ornament--right" role="img" aria-label="Gold filigree corner ornament"></div>
    <div class="brand-mark"></div>
    <div class="brand-name">Noor Verses</div>
    <div class="brand-tagline">LIGHT IN EVERY VERSE</div>
    <h1 class="product-title">QURAN JAR</h1>
  </header>

  <p class="subtitle">A DUA FOR EVERY EMOTION</p>
  <h2 class="headline">READ ME WHEN</h2>

  <svg width="0" height="0" style="position:absolute">
    <defs><polygon id="star" points="22,2 27,16 42,16 30,25 34,40 22,31 10,40 14,25 2,16 17,16"/></defs>
  </svg>

  <div class="emotion emotion--left" style="top:594px"><span class="ar" style="color:var(--happy)">سعيد</span><svg class="star" viewBox="0 0 44 44"><use href="#star" fill="var(--happy)"/></svg><span class="en">HAPPY</span></div>
  <div class="emotion emotion--left" style="top:672px"><span class="ar" style="color:var(--sad)">حزين</span><svg class="star" viewBox="0 0 44 44"><use href="#star" fill="var(--sad)"/></svg><span class="en">SAD</span></div>
  <div class="emotion emotion--left" style="top:749px"><span class="ar" style="color:var(--angry)">غاضب</span><svg class="star" viewBox="0 0 44 44"><use href="#star" fill="var(--angry)"/></svg><span class="en">ANGRY</span></div>

  <div class="book" role="img" aria-label="Illustration of a closed ornate Quran with a green ribbon bookmark"></div>

  <div class="emotion emotion--right" style="top:594px"><span class="ar" style="color:var(--anxious)">قلق</span><svg class="star" viewBox="0 0 44 44"><use href="#star" fill="var(--anxious)"/></svg><span class="en">ANXIOUS</span></div>
  <div class="emotion emotion--right" style="top:678px"><span class="ar" style="color:var(--lonely)">وحيد</span><svg class="star" viewBox="0 0 44 44"><use href="#star" fill="var(--lonely)"/></svg><span class="en">LONELY</span></div>
  <div class="emotion emotion--right" style="top:751px"><span class="ar" style="color:var(--thankful)">شاكرين</span><svg class="star" viewBox="0 0 44 44"><use href="#star" fill="var(--thankful)"/></svg><span class="en">THANKFUL</span></div>

  <div class="banner">COLOUR CODED QURAN VERSES</div>

  <p class="quote">"Do you not see how Allah compares a good word to a good tree?<br>Its root is firm and its branches reach the sky."<br>(Surah Ibrahim 14:24).</p>
</div>
</body>
</html>
```